Pine Ledge Traders, LLC- Global Beverage Company with 100% Cold Chain Logistics

Hey All, My Name is Dale, I am a young business owner in a competitive export space, but my niche is that I am shipping all of my beer around the world, "100% Cold Chain". This model is more costly, but it protects the integrity of the beer itself and will give folks in foreign countries the best representation of what US Craft Beer has to offer.

I am not a branding guy and don't claim to be one, I am a salesperson first, and will be referring to all of you to create something great that will be memorable.

I am looking for a basic Business Card Design for my Craft Beer Export company. I sell US Craft Beer in several countries around the globe. Austrailia, China, Taiwan, Chile, France, New Zealand... to name a few.

I am looking for a sleek, modern, and fresh design. Quickly!

Thanks for your consideration!

Cheers,

Dale

Target Market(s)

International

Contact Information for Business Card

Dale Corrigan
Founder- Roaming Hops Guy
Dale@PineLedgeTraders.example
@RoamingHopsGuy- Instagram only
www.Pineledgetraders.example
@PineLedgeTradersAU- Instagram Only

Font styles to use
Serif

Colors
0592cd
ffffff

Requirements
Must have
• Name-
• Title-
• Email-
• Social Media Handle-
• Company Website-
Nice to have
• Nice Logo/ Images on Card
Should not have
• Tacky Beer Images

```html
<!DOCTYPE html>
<html lang="en">
<head>
<meta charset="utf-8">
<title>Pine Ledge Traders – Business Card</title>
<link rel="stylesheet" href="https://fonts.googleapis.com/css2?family=Cinzel:wght@500;600&family=Cormorant+SC:wght@600&family=Open+Sans:wght@400;600&display=swap">
<style>
  :root {
    --brand-blue: #0592cd;
    --band-blue: #1fa3dc;
    --map-sky: #cdeefa;
    --map-land: #28a9e0;
    --swoosh-gray: #a3a9ad;
    --ink: #3a3a3a;
    --paper: #ffffff;
    --backdrop: #eef1f3;
  }
  * { box-sizing: border-box; margin: 0; padding: 0; }
  html, body {
    width: 1200px; height: 900px; overflow: hidden;
    background: var(--backdrop);
  }
  .canvas {
    width: 1200px; height: 900px;
    display: flex; flex-direction: column; align-items: center; justify-content: center;
    gap: 30px;
  }
  .card {
    position: relative;
    width: 720px; height: 411px;
    background: var(--paper);
    overflow: hidden;
    box-shadow: 0 6px 18px rgba(0,0,0,.15);
  }

  /* Map side */
  .card-map .map-area {
    position: absolute; inset: 0 0 82px 0;
    background: linear-gradient(180deg, var(--map-sky) 0%, #bfe6f7 100%);
  }
  .card-map .map-area .land-tone {
    position: absolute; inset: 18px 40px 10px 30px;
    background: radial-gradient(ellipse at 55% 45%, rgba(40,169,224,.55), rgba(40,169,224,0) 70%);
  }
  .card-map .country-band {
    position: absolute; left: 0; right: 0; bottom: 0; height: 82px;
    background: var(--band-blue);
    display: flex; align-items: center; justify-content: center;
    font-family: "Open Sans", sans-serif; font-size: 19px; color: var(--paper);
    letter-spacing: .3px;
  }

  /* Contact side */
  .card-contact .swoosh { position: absolute; inset: 0; }
  .person { position: absolute; left: 58px; top: 88px; }
  .person-name {
    font-family: "Cinzel", serif; font-weight: 500; font-size: 27px;
    color: var(--brand-blue); letter-spacing: 1px;
  }
  .person-title {
    font-family: "Open Sans", sans-serif; font-weight: 600; font-size: 16px;
    color: var(--ink); margin-top: 2px;
  }
  .company-mark {
    position: absolute; right: 46px; top: 70px;
    display: flex; align-items: center; gap: 12px;
  }
  .company-mark .mark-square {
    width: 34px; height: 34px; background: var(--brand-blue);
  }
  .company-mark .company-name {
    font-family: "Cinzel", serif; font-weight: 500; font-size: 26px;
    color: var(--brand-blue); line-height: 1.05;
  }
  .contacts {
    position: absolute; left: 58px; top: 222px;
    font-family: "Open Sans", sans-serif; font-size: 17px; color: var(--ink);
    list-style: none;
  }
  .contacts li { display: flex; align-items: center; gap: 8px; height: 26px; }
  .contacts .social { margin-bottom: 8px; }
  .contacts .dot {
    width: 22px; height: 22px; border-radius: 50%; background: var(--brand-blue);
  }
  .contacts svg { width: 16px; height: 16px; flex: none; }
  .cold-chain {
    position: absolute; right: 30px; top: 334px;
    font-family: "Cormorant SC", serif; font-weight: 600; font-size: 23px;
    line-height: 1.1;
    color: var(--paper); letter-spacing: .5px;
    white-space: nowrap;
  }
</style>
</head>
<body>
<main class="canvas">

  <section class="card card-map">
    <div class="map-area" role="img" aria-label="World map with continents in blue on a light blue ocean">
      <div class="land-tone"></div>
    </div>
    <div class="country-band">Austrailia | China | Taiwan | Chile | France | New Zealand</div>
  </section>

  <section class="card card-contact">
    <svg class="swoosh" viewBox="0 0 720 411" preserveAspectRatio="none" aria-hidden="true">
      <path d="M0,322 C160,380 320,330 460,250 C550,200 640,178 720,174 L720,411 L0,411 Z" fill="var(--swoosh-gray)"/>
      <path d="M0,352 C150,398 330,352 470,272 C560,220 650,202 720,198 L720,411 L0,411 Z" fill="var(--brand-blue)"/>
      <path d="M0,352 C150,398 330,352 470,272 C560,220 650,202 720,198" fill="none" stroke="var(--paper)" stroke-width="4"/>
    </svg>

    <div class="company-mark">
      <span class="mark-square"></span>
      <span class="company-name">Pine Ledge<br>Traders</span>
    </div>

    <div class="person">
      <h1 class="person-name">DALE CORRIGAN</h1>
      <p class="person-title">Founder - Roaming Hops Guy</p>
    </div>

    <ul class="contacts">
      <li class="social"><span class="dot"></span>@RoamingHopsGuy</li>
      <li>
        <svg viewBox="0 0 16 16" aria-hidden="true"><rect x="1" y="3" width="14" height="10" fill="var(--brand-blue)"/><path d="M1,3 L8,9 L15,3" fill="none" stroke="#fff" stroke-width="1.4"/></svg>
        Dale@PineLedgeTraders.example
      </li>
      <li>
        <svg viewBox="0 0 16 16" aria-hidden="true"><circle cx="8" cy="8" r="7" fill="var(--brand-blue)"/><ellipse cx="8" cy="8" rx="3" ry="7" fill="none" stroke="#fff" stroke-width="1"/><line x1="1" y1="8" x2="15" y2="8" stroke="#fff" stroke-width="1"/></svg>
        www.Pineledgetraders.example
      </li>
    </ul>

    <p class="cold-chain">100% Cold Chain Logistics</p>
  </section>

</main>
</body>
</html>
```